Dalvick's Business Card

I need some designs for a new business card including the new logo attached. An old example of our business card is also attached to show all the data that should be included on the new design.
**I added some more examples someone had mocked up**

Contact Information for Business Card

Should include all info on other examples uploaded.

```html
<!DOCTYPE html>
<html lang="en">
<head>
<meta charset="utf-8">
<title>Dalvick's Business Card</title>
<link href="https://fonts.googleapis.com/css2?family=Montserrat:wght@400;600;700;800&display=swap" rel="stylesheet">
<style>
  :root {
    --backdrop: #9a9b9c;
    --card: #f4f4f5;
    --blue: #0d4fa8;
    --red: #c8090f;
    --emboss: #e6e6e8;
  }
  * { margin: 0; padding: 0; box-sizing: border-box; }
  html, body { width: 1200px; height: 1200px; overflow: hidden; }
  body {
    background: var(--backdrop);
    font-family: "Montserrat", sans-serif;
    position: relative;
  }
  .card {
    position: absolute;
    left: 207px;
    width: 796px;
    height: 441px;
    background: var(--card);
    overflow: hidden;
    box-shadow: 0 12px 22px rgba(0,0,0,0.28);
  }
  .card--front { top: 106px; }
  .card--back { top: 641px; }

  .brand-dot { position: absolute; border-radius: 50%; background: var(--blue); }
  .brand-name { position: absolute; color: var(--blue); font-weight: 700; line-height: 1; white-space: nowrap; }
  .brand-service { position: absolute; color: var(--red); font-weight: 700; line-height: 1; white-space: nowrap; }

  .card--front .brand-dot { left: 55px; top: 62px; width: 78px; height: 78px; }
  .card--front .brand-name { left: 147px; top: 78px; font-size: 48px; }
  .card--front .brand-service { left: 147px; top: 122px; font-size: 12.5px; }

  .emboss-mark {
    position: absolute; left: 495px; top: 100px;
    width: 230px; height: 230px; border-radius: 50%;
    background: var(--emboss);
    box-shadow: inset 2px 2px 4px rgba(0,0,0,0.10), inset -2px -2px 4px rgba(255,255,255,0.9);
  }

  .contact-name {
    position: absolute; left: 57px; top: 224px;
    color: var(--red); font-weight: 800; font-size: 34px; letter-spacing: 0.3px;
  }
  .contact-line {
    position: absolute; left: 57px; display: flex; align-items: center;
    color: var(--blue); font-size: 23px; font-weight: 400;
  }
  .contact-line svg { width: 20px; height: 20px; margin-right: 10px; fill: var(--red); }
  .contact-line--phone { top: 274px; }
  .contact-line--email { top: 309px; }

  .front-bands { position: absolute; left: 0; top: 383px; width: 796px; height: 58px; }
  .band-label {
    position: absolute; top: 400px; color: #fff; font-size: 20px; font-weight: 400; letter-spacing: 0.4px;
  }
  .band-label--left { left: 57px; }
  .band-label--right { left: 421px; }

  .card--back .brand-dot { left: 105px; top: 135px; width: 142px; height: 142px; }
  .card--back .brand-name { left: 255px; top: 158px; font-size: 82px; }
  .card--back .brand-service { left: 257px; top: 236px; font-size: 20px; }
  .service-area {
    position: absolute; left: 257px; top: 142px; width: 435px; text-align: right;
    color: var(--red); font-weight: 600; font-size: 14.5px; line-height: 1; letter-spacing: 0.2px; white-space: nowrap;
  }
  .call-to-action {
    position: absolute; left: 0; width: 100%; top: 348px; text-align: center;
    color: var(--blue); font-weight: 600; font-size: 17.5px; line-height: 25px;
  }
  .back-band { position: absolute; top: 419px; height: 22px; }
  .back-band--left { left: 0; width: 199px; background: var(--blue); }
  .back-band--mid { left: 214px; width: 369px; background: var(--red); }
  .back-band--right { left: 597px; width: 199px; background: var(--blue); }
</style>
</head>
<body>

<section class="card card--front">
  <span class="brand-dot"></span>
  <span class="brand-name">DALVICK'S</span>
  <span class="brand-service">AIR CONDITIONING &amp; HEATING SERVICE</span>

  <div class="emboss-mark"></div>

  <h1 class="contact-name">MARK DALVICK</h1>
  <div class="contact-line contact-line--phone">
    <svg viewBox="0 0 24 24"><path d="M6.6 10.8a15 15 0 0 0 6.6 6.6l2.2-2.2c.3-.3.7-.4 1-.2 1.1.4 2.3.6 3.6.6.6 0 1 .4 1 1V20c0 .6-.4 1-1 1C10.6 21 3 13.4 3 4c0-.6.4-1 1-1h3.5c.6 0 1 .4 1 1 0 1.3.2 2.5.6 3.6.1.3 0 .7-.2 1z"/></svg>
    555.018.2740
  </div>
  <div class="contact-line contact-line--email">
    <svg viewBox="0 0 24 24"><path d="M2 5h20v2l-10 6L2 7z"/><path d="M2 9l10 6 10-6v10H2z"/></svg>
    dalvickhvac@example.com
  </div>

  <svg class="front-bands" viewBox="0 0 796 58">
    <path d="M0 0 H322 Q352 0 372 18 L412 58 H0 Z" fill="var(--blue)"/>
    <path d="M372 0 Q358 0 364 9 L398 58 H796 V0 Z" fill="var(--red)"/>
  </svg>
  <span class="band-label band-label--left">LICENSED &amp; INSURED</span>
  <span class="band-label band-label--right">FAMILY OWNED &amp; OPERATED</span>
</section>

<section class="card card--back">
  <p class="service-area">SERVES MAPLE RIDGE, IA &amp; SURROUNDING AREAS</p>
  <span class="brand-dot"></span>
  <span class="brand-name">DALVICK'S</span>
  <span class="brand-service">AIR CONDITIONING &amp; HEATING SERVICE</span>

  <p class="call-to-action">CALL TODAY FOR ALL YOUR HVAC,<br>REFRIGERATION &amp; PLUMBING NEEDS</p>

  <span class="back-band back-band--left"></span>
  <span class="back-band back-band--mid"></span>
  <span class="back-band back-band--right"></span>
</section>

</body>
</html>
```